Lumavento business card

We need a modern business card - With our 4 colors - See web: www.lumavento.dk

I have attached logo and som old business Cards we have - Lets Make the new ones shine...:-) -

Industry/Entity Type

Business

Requirements
Must have
• the logo with lumavento only,

```html
<!DOCTYPE html>
<html lang="da">
<head>
<meta charset="utf-8">
<title>Lumavento visitkort</title>
<link rel="stylesheet" href="https://fonts.googleapis.com/css2?family=Source+Sans+3:wght@300;400;600&display=swap">
<style>
  :root {
    --stage: #000000;
    --card: #333336;
    --lime: #a6ce39;
    --magenta: #e5177d;
    --orange: #f0821e;
    --purple: #7b3f8e;
    --light: #e2e2e2;
    --soft: #cfcfcf;
    --divider: #3d3d40;
  }
  * { margin: 0; padding: 0; box-sizing: border-box; }
  html, body { width: 1200px; height: 900px; overflow: hidden; background: var(--stage); }
  body { position: relative; font-family: "Source Sans 3", sans-serif; }

  .card {
    position: absolute;
    top: 271px;
    width: 457px;
    height: 281px;
    border-radius: 14px;
    background: var(--card);
  }
  .card--front { left: 137px; }
  .card--back { left: 626px; }

  /* front */
  .front-brand {
    position: absolute;
    left: 44px;
    top: 122px;
    display: flex;
    align-items: center;
    gap: 10px;
    color: var(--lime);
    font-size: 24px;
    font-weight: 400;
    letter-spacing: 1px;
  }
  .brand-dot {
    width: 16px; height: 16px;
    border-radius: 50%;
    background: var(--lime);
  }
  .front-divider {
    position: absolute;
    left: 208px; top: 70px;
    width: 1px; height: 130px;
    background: var(--divider);
  }
  .details {
    position: absolute;
    left: 233px; top: 64px;
    color: var(--lime);
    font-size: 12.5px;
    line-height: 16px;
  }
  .person-name { font-size: 16.5px; font-weight: 600; line-height: 20px; }
  .person-name .first { color: var(--magenta); }
  .person-name .last { color: var(--orange); }
  .person-title { margin-bottom: 20px; }
  .address { margin-bottom: 15px; }
  .contact-list { list-style: none; }
  .contact-list li { display: flex; align-items: center; gap: 8px; height: 19px; }
  .contact-list svg { width: 10px; height: 10px; flex: none; margin-left: 2px; }

  /* back */
  .back-mark {
    position: absolute;
    left: 50%; top: 62px;
    width: 34px; height: 34px;
    margin-left: -17px;
    border-radius: 50%;
    background: var(--lime);
  }
  .back-wordmark {
    position: absolute;
    left: 0; right: 0; top: 162px;
    text-align: center;
    color: var(--light);
    font-size: 21px;
    font-weight: 300;
    letter-spacing: 3.5px;
  }
  .back-rule {
    position: absolute;
    left: 102px; top: 201px;
    width: 254px; height: 3px;
    background: var(--lime);
  }
  .tagline {
    position: absolute;
    left: 0; right: 0; top: 216px;
    text-align: center;
    color: var(--soft);
    font-size: 15px;
    font-weight: 300;
  }
</style>
</head>
<body>
  <section class="card card--front" aria-label="Visitkort forside">
    <div class="front-brand"><span class="brand-dot"></span>lumavento</div>
    <div class="front-divider"></div>
    <div class="details">
      <p class="person-name"><span class="first">Sigrid</span> <span class="last">Holmvang</span></p>
      <p class="person-title">Salgsdirektør</p>
      <p class="address">Kastanjevej 14 - 2100<br>Østerby -Tlf. 36 41 72 08</p>
      <ul class="contact-list">
        <li>
          <svg viewBox="0 0 10 10" aria-hidden="true"><path fill="var(--magenta)" d="M2 0.5 L3.6 2.6 L2.7 3.6 Q3.8 5.9 6.4 7.3 L7.4 6.4 L9.5 8 L8.3 9.5 Q3.5 8.8 0.5 1.7 Z"/></svg>
          +45 61 24 83 97
        </li>
        <li>
          <svg viewBox="0 0 10 10" aria-hidden="true"><rect x="0.5" y="2" width="9" height="6.5" fill="var(--orange)"/><path d="M0.8 2.3 L5 5.6 L9.2 2.3" fill="none" stroke="var(--card)" stroke-width="1"/></svg>
          sh@lumavento.dk
        </li>
        <li>
          <svg viewBox="0 0 10 10" aria-hidden="true"><circle cx="5" cy="5" r="4.6" fill="var(--purple)"/><path d="M3 2.5 Q4.5 3.5 4 5 Q6 5.5 6.5 8 M6.5 1.5 Q7 3 8.6 3.5" fill="none" stroke="var(--card)" stroke-width="0.9"/></svg>
          www.lumavento.dk
        </li>
      </ul>
    </div>
  </section>

  <section class="card card--back" aria-label="Visitkort bagside">
    <div class="back-mark"></div>
    <p class="back-wordmark">lumavento</p>
    <div class="back-rule"></div>
    <p class="tagline">Medier til unge</p>
  </section>
</body>
</html>
```